dravo hire pricelist

Hi There,

Can we please edit this price list?

The borders need to be lined up and all color coordinated for us.

There are quite a few areas where everything is misjoined and not lining up correctly.

```html
<!DOCTYPE html>
<html lang="en">
<head>
<meta charset="utf-8">
<title>Dravo Hire Price List</title>
<link href="https://fonts.googleapis.com/css2?family=Montserrat:wght@600;700;800&family=Open+Sans:ital,wght@0,400;0,600;0,700;1,600&display=swap" rel="stylesheet">
<style>
  :root{
    --green:#7dc242;
    --green-soft:#c9d9b5;
    --ink:#1c1c1c;
    --black:#0b0b0b;
    --cell:#f0f0f0;
    --rule:#b8b8b8;
    --paper:#ffffff;
    --backdrop:#ececec;
    --white:#ffffff;
  }
  *{box-sizing:border-box;margin:0;padding:0}
  html,body{width:1200px;height:850px;overflow:hidden}
  body{background:var(--backdrop);font-family:"Open Sans",sans-serif;color:var(--ink);position:relative}
  .page{position:absolute;top:13px;width:577px;height:816px;background:var(--paper);box-shadow:2px 3px 6px rgba(0,0,0,.35);overflow:hidden}
  .page--one{left:15px}
  .page--two{left:605px}
  .hero{position:relative;height:117px;background:linear-gradient(100deg,#2a2a2a 0%,#4a4a47 45%,#3a3a38 70%,#1f1f1f 100%)}
  .hero__brand{position:absolute;left:36px;top:46px;display:flex;align-items:center;gap:9px}
  .hero__brand-dot{width:16px;height:16px;border-radius:50%;background:var(--green)}
  .hero__brand-name{font-family:"Open Sans",sans-serif;font-weight:700;font-size:24px;line-height:1;color:var(--white)}
  .hero__tagline{position:absolute;left:443px;top:30px;font-family:"Montserrat",sans-serif;font-weight:800;font-size:14.2px;line-height:16.5px;color:#fff}
  .hero__tagline .accent{color:var(--green)}
  .contact-bar{height:22px;background:var(--black);display:flex;align-items:center;justify-content:space-between;padding:0 25px;color:#fff;font-family:"Montserrat",sans-serif;font-weight:800;font-size:10px;border-right:5px solid var(--green)}
  .contact-bar .sep{width:2px;height:14px;background:#fff}
  .notice{margin-top:9px;text-align:center;font-weight:700;font-size:7.3px;line-height:9px}
  .columns{position:absolute;top:161px;left:28px;display:flex;gap:8px}
  .col{width:255px}
  .price-table{width:100%;border-collapse:collapse;table-layout:fixed;margin-bottom:2.5px}
  .price-table th{height:14px;background:var(--green);color:#fff;font-family:"Montserrat",sans-serif;font-weight:700;font-size:6.4px;letter-spacing:-.1px;text-align:center;white-space:nowrap;overflow:hidden;border-right:1px solid rgba(255,255,255,.45)}
  .price-table th:last-child{border-right:0}
  .price-table th.item{width:66%}
  .price-table th.num{width:17%}
  .price-table td{height:13.6px;background:var(--cell);border:.6px solid var(--rule);font-size:6.5px;line-height:12px;white-space:nowrap;overflow:hidden}
  .price-table td:first-child{padding-left:9px}
  .price-table td:not(:first-child){text-align:center}
  .price-table td.span-note{background:var(--green-soft);text-align:center}
  .footer{position:absolute;left:0;right:0;bottom:0;height:20px;background:var(--black);color:#fff;display:flex;align-items:center}
  .footer__terms{position:absolute;left:150px;width:305px;text-align:center;font-style:italic;font-weight:600;font-size:5.6px}
  .footer__page{position:absolute;right:28px;font-family:"Montserrat",sans-serif;font-weight:800;font-size:9px}
</style>
</head>
<body>

<section class="page page--one">
  <header class="hero" role="img" aria-label="Photo of construction workers in hard hats with a scissor lift">
    <div class="hero__brand"><span class="hero__brand-dot"></span><span class="hero__brand-name">Dravo Hire</span></div>
    <div class="hero__tagline">THE<br><span class="accent">CONSTRUCTION</span><br>INDUSTRY<br>SPECIALISTS</div>
  </header>
  <div class="contact-bar"><span>CALL US TODAT (03) 9555 0142</span><span class="sep"></span><span>EMAIL : hire@dravohire.com.au</span><span class="sep"></span><span>www.dravohire.com.au</span></div>
  <p class="notice">Mobile scaffold tower $ 50 per vertical metre - per week - $ 80 delivery e/w - erection by licensed scaffolders available. Melbourne Metroute deliveries $ 50</p>
  <div class="columns">
    <div class="col">
      <table class="price-table"><tr><th class="item">LADDERS AND TRESTLES</th><th class="num">DAILY</th><th class="num">WEEKLY</th></tr>
        <tr><td>Adjustable Props #0-#4 (Min 1 Week)<td>$ 14.50<td>$ 14.50
        <tr><td>Extension Ladder 15/21 Ft<td>$ 30.00<td>$ 60.00
        <tr><td>Extension Ladder 15/21 Ft<td>$ 30.00<td>$ 60.00
        <tr><td>Step Ladder 6ft - 8ft<td>$ 30.00<td>$ 60.00
        <tr><td>Step Ladder 10ft - 12ft<td>$ 30.00<td>$ 60.00
        <tr><td>Trestles (Each) 6ft - 12 ft<td>$ 30.00<td>$ 60.00
        <tr><td>Planks 4m, 5m, 6m (Aluminium)<td>$ 18.00<td>$ 35.00
        <tr><td>Alluminium Scaffold Towers<td colspan="2" class="span-note">$ 50 Vertical Meter
      </table>
      <table class="price-table"><tr><th class="item">AIR/HYDRAULIC TOOLS</th><th class="num">DAILY</th><th class="num">WEEKLY</th></tr>
        <tr><td>Compressor (CFM Electric)<td>$ 66.00<td>$ 225.00
        <tr><td>Compressor Hose &amp; Nail Gun<td>$ 118.80<td>$ 363.00
        <tr><td>Coil Nail Gun<td>$ 66.00<td>$ 198.00
        <tr><td>Nail Gun - Framing<td>$ 59.40<td>$ 198.00
        <tr><td>Nail Gun - Gas<td>$ 99.00<td>$ 363.00
        <tr><td>Secret Nail Gun<td>$ 72.00<td>$ 231.00
        <tr><td>Staple Gun<td>$ 52.80<td>$ 198.00
      </table>
      <table class="price-table"><tr><th class="item">PLASTER,CEILING AND ROOF TOOLS</th><th class="num">DAILY</th><th class="num">WEEKLY</th></tr>
        <tr><td>Panel Left<td>$ 66.00<td>$ 210.00
      </table>
      <table class="price-table"><tr><th class="item">LASER LEVELS AND MEASURING TOOLS</th><th class="num">DAILY</th><th class="num">WEEKLY</th></tr>
        <tr><td>Laser Level Tripod and Staff<td>$ 99.00<td>$ 380.00
        <tr><td>Tape Measure 60m<td>$ 15.84<td>$ 15.84
      </table>
      <table class="price-table"><tr><th class="item">TARPAULINS</th><th class="num">DAILY</th><th class="num">WEEKLY</th></tr>
        <tr><td>Tarpaulins 6m x 9m<td><td>$ 84.00
      </table>
      <table class="price-table"><tr><th class="item">TEMPORARY FENCING</th><th class="num">DAILY</th><th class="num">WEEKLY</th></tr>
        <tr><td>Temporary Fencing - Per Meter Per Month<td><td>4.20 P/M
      </table>
      <table class="price-table"><tr><th class="item">TOILETS</th><th class="num">DAILY</th><th class="num">WEEKLY</th></tr>
        <tr><td>Portable Toilet<td><td>$ 45.00
        <tr><td>Toilet Pumpouts - $85<td><td>
        <tr><td>Sewer Connected Toilet<td><td>$ 45.00
        <tr><td>Toilet on Trailer<td>$ 120.00<td>$ 300.00
      </table>
      <table class="price-table"><tr><th class="item">CLEANING EQUIPMENT AND PUMP</th><th class="num">DAILY</th><th class="num">WEEKLY</th></tr>
        <tr><td>Flex Drive Pump<td>$ 66.00<td>$ 145.00
        <tr><td>Flex Drive Motor<td>$ 66.00<td>$ 145.00
        <tr><td>Sub Pump 2 - Float or Non Float<td>$ 79.20<td>$ 185.00
      </table>
      <table class="price-table"><tr><th class="item">VACCUM CLEANERS</th><th class="num">DAILY</th><th class="num">WEEKLY</th></tr>
        <tr><td>Vaccum Cleaner 2 Motor Industrial/Wet &amp; Dry<td>$ 86.00<td>$ 290.00
        <tr><td>Vaccum Cleaner - Plaster Dust<td>$ 105.00<td>$ 572.00
      </table>
      <table class="price-table"><tr><th class="item">PRESSURE CLEANERS</th><th class="num">DAILY</th><th class="num">WEEKLY</th></tr>
        <tr><td>Electric Pressure Washer 2000PSI<td>$ 125.40<td>$ 290.00
        <tr><td>Petrol Pressure Washer 4000 PSI<td>$ 158.40<td>$ 572.00
      </table>
      <table class="price-table"><tr><th class="item">PRESSURE CLEANERS</th><th class="num">DAILY</th><th class="num">WEEKLY</th></tr>
        <tr><td>Electric Pressure Washer 2000PSI<td>$ 125.40<td>$ 290.00
        <tr><td>Petrol Pressure Washer 4000 PSI<td>$ 158.40<td>$ 572.00
      </table>
    </div>
    <div class="col">
      <table class="price-table"><tr><th class="item">CONCRETE EQUIPMENT</th><th class="num">DAILY</th><th class="num">WEEKLY</th></tr>
        <tr><td>Concrete Screed 2m / 3m<td>$ 18.00<td>$ 52.00
        <tr><td>Trowelling Machine (Petrol)<td>$ 93.50<td>$ 374.00
      </table>
      <table class="price-table"><tr><th class="item">GRINDERS, PLANERS AND MOWERS</th><th class="num">DAILY</th><th class="num">WEEKLY</th></tr>
        <tr><td>Concrete Floor Grinder” (Diamond extra)<td>$ 105.60<td>$ 364.00
        <tr><td>9 Inch Grinder with Diamond Disc<td>$ 88.00<td>$ 320.00
        <tr><td>Concrete Dust Vaccum Cleaner<td>$ 105.60<td>$ 340.00
      </table>
      <table class="price-table"><tr><th class="item">CONCRETE/BRICK SAWS AND CUTTER</th><th class="num">DAILY</th><th class="num">WEEKLY</th></tr>
        <tr><td>Demo Saw 14”<td>$ 158.00<td>$ 550.00
        <tr><td>Demo Saw 16”<td>$ 158.00<td>$ 550.00
        <tr><td>Pedestrian Concrete Saw 18”<td>$ 198.00<td>$ 607.00
      </table>
      <table class="price-table"><tr><th class="item">AIR TOOLS HEAVY DUTY</th><th class="num">DAILY</th><th class="num">WEEKLY</th></tr>
        <tr><td>Compressor (130 CFM Diesel)<td>$ 171.00<td>$ 550.00
        <tr><td>Beam Blower<td>$ 13.00<td>$ 40.00
        <tr><td>Breaker Heavy<td>$ 66.00<td>$ 132.00
      </table>
      <table class="price-table"><tr><th class="item">BRICK/CONCRETE, TIMBER AND TILE TOOLS</th><th class="num">DAILY</th><th class="num">WEEKLY</th></tr>
        <tr><td>Brick Saw / Paver Inc. Diamond Blade<td>$ 145.00<td>$ 420.00
        <tr><td>Demo Saw 16” (Blade included)<td>$ 158.00<td>$ 550.00
        <tr><td>Pedestrian Concrete Saw<td>$ 198.00<td>$ 528.00
        <tr><td>Wall Chaser<td>$ 141.00<td>$ 450.00
        <tr><td>Grinder 225mm (Diamond Blade)<td>$ 105.00<td>$ 290.00
        <tr><td>Mortar Rake Saw (Brick &amp; Mortar Saw)<td>$ 120.00<td>$ 420.00
        <tr><td>Sebre Saw<td>$ 46.00<td>$ 165.00
        <tr><td>Saw Circular 235mm<td>$ 52.80<td>$ 145.00
        <tr><td>Core Hole Drill - (Diamond extra)<td>$ 200.00<td>$ 600.00
        <tr><td>Jamb Saw<td>$ 140.00<td>$ 480.00
        <tr><td>Tile Saw 900mm<td>$ 145.00<td>$ 420.00
        <tr><td>Lock Mortiser<td>$ 191.00<td>$ 540.00
        <tr><td>Wood Router<td>$ 46.00<td>$ 165.00
      </table>
      <table class="price-table"><tr><th class="item">DRILLS</th><th class="num">DAILY</th><th class="num">WEEKLY</th></tr>
        <tr><td>Cordless Hand Drill/Driver<td>$ 39.60<td>$ 184.00
        <tr><td>Drill Magnetic<td>$ 132.00<td>$ 462.00
        <tr><td>Plaster Screw Gun<td>$ 55.00<td>$ 180.00
        <tr><td>Fastning Gun<td>$ 60.00<td>$ 198.00
        <tr><td>Drill Bits (All Makes)<td>$ 13.00<td>$ 53.00
        <tr><td>Impact Hammer Drill<td>$ 72.00<td>$ 264.00
        <tr><td>Hemmer Drill Bits<td>$ 12.00<td>$ 38.00
      </table>
      <table class="price-table"><tr><th class="item">JACKHAMMERS</th><th class="num">DAILY</th><th class="num">WEEKLY</th></tr>
        <tr><td>Jackhammer Small Electric<td>$ 65.00<td>$ 255.00
        <tr><td>Jackhammer Medium<td>$ 71.00<td>$ 286.00
        <tr><td>Jackhammer Large<td>$ 112.00<td>$ 440.00
        <tr><td>Tile Remover Attachment<td>$ 39.00<td>$ 158.00
        <tr><td>Spade Tool (All Makes)<td>$ 13.00<td>$ 48.00
      </table>
      <table class="price-table"><tr><th class="item">SAFETY EQUIPMENT</th><th class="num">DAILY</th><th class="num">WEEKLY</th></tr>
        <tr><td>Road Safety Harness Kit<td>$ 24.00<td>$ 84.00
      </table>
    </div>
  </div>
  <footer class="footer"><span class="footer__terms">*Prices effective 24/01/2022 and are subject to change without notice. All prices are exclusive of GST</span><span class="footer__page">Page 1 of 2</span></footer>
</section>

<section class="page page--two">
  <header class="hero" role="img" aria-label="Photo of construction workers in hard hats with a scissor lift">
    <div class="hero__brand"><span class="hero__brand-dot"></span><span class="hero__brand-name">Dravo Hire</span></div>
    <div class="hero__tagline">THE<br><span class="accent">CONSTRUCTION</span><br>INDUSTRY<br>SPECIALISTS</div>
  </header>
  <div class="contact-bar"><span>CALL US TODAT (03) 9555 0142</span><span class="sep"></span><span>EMAIL : hire@dravohire.com.au</span><span class="sep"></span><span>www.dravohire.com.au</span></div>
  <p class="notice">Mobile scaffold tower $50 per vertical metre - per week - $80 deliver e/w - erection by licensed scaffolders availabe.</p>
  <div class="columns">
    <div class="col">
      <table class="price-table"><tr><th class="item">EARTHMOVING, MINI LOADERS, ATTACHMENTS</th><th class="num">DAILY</th><th class="num">WEEKLY</th></tr>
        <tr><td>Mini Loader - Korva - Large or Small<td>$ 300.00<td>$ 1,000.00
        <tr><td>Veltro Tracked Dumper<td>$ 180.00<td>$ 700.00
        <tr><td>Mini Loader c/w Post Hole Digger<td>$ 336.00<td>$ 1,280.00
        <tr><td>Mini Loader c/w Trencher<td>$ 372.00<td>$ 1,152.00
      </table>
      <table class="price-table"><tr><th class="item">EXCAVATORS</th><th class="num">DAILY</th><th class="num">WEEKLY</th></tr>
        <tr><td>Mini Excavator - 1 Tonne - Min 740 Wide<td>$ 240.00<td>$ 1,100.00
        <tr><td>Mini Excavator - 1.7 Tonne - 980 Wide<td>$ 240.00<td>$ 1,100.00
        <tr><td>Excavator - 3.5 Tonne - Trans $180<td>$ 320.00<td>$ 1,300.00
        <tr><td>Excavator - 5 Tonne - Trans $240<td>$ 420.00<td>$ 1,600.00
        <tr><td>Excavator - 8 Tonne - Trans $300<td>$ 460.00<td>$ 1,800.00
        <tr><td>Excavator up to 22 Tonne<td>P.O.A<td>
        <tr><td>1.7T Breaker - 8T Breaker<td>$ 180.00<td>$ 500.00
        <tr><td>3.5T Breaker - 8T Breaker<td>$ 220.00<td>$ 650.00
        <tr><td>Augers Ranging From 250mm to 600mm<td>$ 160.00<td>$ 450.00
      </table>
      <table class="price-table"><tr><th class="item">MATERIALS HANDLING</th><th class="num">DAILY</th><th class="num">WEEKLY</th></tr>
        <tr><td>Glass Sucker (Per Pair)<td>$ 24.00<td>$ 39.60
        <tr><td>Piano Trolley<td>$ 29.00<td>$ 79.20
        <tr><td>Hand Trolley<td>$ 23.76<td>$ 66.00
        <tr><td>Pallet Truck (2000 kg)<td>$ 39.60<td>$ 118.80
        <tr><td>Brick / Block Elevator 6m<td>$ 125.40<td>$ 396.00
        <tr><td>Brick / Block Elevator 9m<td>$ 145.00<td>$ 480.00
        <tr><td>Chain Block Half Ton / 1 Ton / 2 Ton<td>$ 39.60<td>$ 132.00
        <tr><td>Forklift Gas Operated 2.5 Ton<td>$ 150.00<td>$ 350.00
        <tr><td>Forklift Diesel 2.5T RT Buggy<td>$ 220.00<td>$ 800.00
        <tr><td>Concrete Kibble 1m<td>$ 150.00<td>$ 350.00
        <tr><td>Concrete Kibble 1.5m<td>$ 150.00<td>$ 350.00
        <tr><td>Concrete Kibble Truck<td>$ 50.00<td>$ 150.00
        <tr><td>Brick &amp; Block Cage<td>$ 110.00<td>$ 290.00
        <tr><td>Gas Cage<td><td>$ 80.00
        <tr><td>Bin Lifter<td>$ 110.00<td>$ 250.00
      </table>
      <table class="price-table"><tr><th class="item">SKID STEERS</th><th class="num">DAILY</th><th class="num">WEEKLY</th></tr>
        <tr><td>Skid Steer 1.2m wide Standard<td>$ 312.00<td>$ 1,080.00
        <tr><td>Korrin TL - 50 Compact - Track Loader<td>$ 400.00<td>$ 1,600.00
      </table>
      <table class="price-table"><tr><th class="item">LIGHTS</th><th class="num">DAILY</th><th class="num">WEEKLY</th></tr>
        <tr><td>Floodlight 500W Twin On Stand<td>$ 23.76<td>$ 47.52
        <tr><td>Light Tower<td>$ 180.00<td>$ 450.00
      </table>
      <table class="price-table"><tr><th class="item">HOISTS AND LIFTER</th><th class="num">DAILY</th><th class="num">WEEKLY</th></tr>
        <tr><td>Duct Lifter - 250 kg Capacity<td>$ 118.80<td>$ 440.00
        <tr><td>Panel Lift<td>$ 59.40<td>$ 237.60
      </table>
      <table class="price-table"><tr><th class="item">CONCRETE VIBRATORS</th><th class="num">DAILY</th><th class="num">WEEKLY</th></tr>
        <tr><td>Flex Drive Shaft (Portable)<td>$ 79.20<td>$ 330.00
        <tr><td>Flex Drive Motor (Petrol)<td>$ 66.00<td>$ 145.20
        <tr><td>Flex Drive Shaft - Concrete Vibe<td>$ 39.60<td>$ 132.00
      </table>
    </div>
    <div class="col">
      <table class="price-table"><tr><th class="item">TRAFFIC</th><th class="num">DAILY</th><th class="num">WEEKLY</th></tr>
        <tr><td>TRAFFIC Barricade Bollards<td>$ 1.00+<td>$ 6.60
        <tr><td>Barricade Lights<td>$ 10.56<td>$ 39.60
        <tr><td>Roadplates - 2.4m x 1.2m (Transport P.O.A)<td><td>$ 110.00
        <tr><td>Barrier-Water Filled TL2 Crash Barrier (Per metre)<td>$ 1.75<td>$ 12.25
      </table>
      <table class="price-table"><tr><th class="item">FANS AND HEATERS</th><th class="num">DAILY</th><th class="num">WEEKLY</th></tr>
        <tr><td>Fan Carpet Dryer<td>$ 59.40<td>$ 184.80
        <tr><td>Fan Carpet Dryer<td>$ 78.00<td>$ 380.00
        <tr><td>Exhaust Fan w/Ducting / 600mm<td>$ 59.40<td>$ 145.20
        <tr><td>Exhaust Fan Ducting $3 Per meter<td><td>
      </table>
      <table class="price-table"><tr><th class="item">HEATER</th><th class="num">DAILY</th><th class="num">WEEKLY</th></tr>
        <tr><td>Heater Blower Small / Large (Gas Extra)<td>$ 79.20<td>$ 110.00
        <tr><td>Gas Bottle - Medium - $80 - Large - $160<td><td>
      </table>
      <table class="price-table"><tr><th class="item">CONCRETE MIXERS</th><th class="num">DAILY</th><th class="num">WEEKLY</th></tr>
        <tr><td>Mixer Electric<td>$ 132.00<td>$ 158.40
      </table>
      <table class="price-table"><tr><th class="item">FLOOD SANDERS</th><th class="num">DAILY</th><th class="num">WEEKLY</th></tr>
        <tr><td>Floor Edger<td>$ 79.20<td>$ 224.40
        <tr><td>Floor Sander 7” Drum - Sand Pads $8<td>$ 112.20<td>$ 330.00
        <tr><td>Wallpaper Streamer<td>$ 80.00<td>$ 260.00
      </table>
      <table class="price-table"><tr><th class="item">GENERATORS</th><th class="num">DAILY</th><th class="num">WEEKLY</th></tr>
        <tr><td>Generator (8KVA)<td>$ 110.00<td>$ 380.00
        <tr><td>Generator (10KVA)<td>$ 110.00<td>$ 380.00
        <tr><td>16KVA Generator with 3 phase<td>$ 200.00<td>$ 450.00
        <tr><td>25KVA Diesel Generator<td>$ 200.00<td>$ 550.00
      </table>
      <table class="price-table"><tr><th class="item">LAWN AND TURF CARE</th><th class="num">DAILY</th><th class="num">WEEKLY</th></tr>
        <tr><td>Whipper Snipper<td>$ 36.00<td>$ 132.00
        <tr><td>Lawn Mower (4 Stroke)<td>$ 43.56<td>$ 132.00
        <tr><td>Post - Hole Digger one man / 200mm<td>$ 99.00<td>$ 330.00
        <tr><td>Post - Hole Digger 2 - Man<td>$ 118.80<td>$ 448.80
        <tr><td>Leaf Blower (2 Stroke)<td>$ 39.60<td>$ 132.00
        <tr><td>Rotary Hoe<td>$ 130.00<td>$ 450.00
      </table>
    </div>
  </div>
  <footer class="footer"><span class="footer__terms">*Prices effective 01/02/2019 and are subject to change withour notice.All prices are exclusive of GST</span><span class="footer__page">Page 2 of 2</span></footer>
</section>

</body>
</html>
```